Camp Thornbrook 2021 Magazine Design

We are for someone to design our annual magazine/newsletter. This is a print newsletter that is a total of 20 pages. It will need to be designed in a way that is easy to share with our printers. The designer will need to be someone who is creative and easy to work with.
For those interested in this project we ask that you design 4 to 6 pages for us to view. Once we select the designer we will want the rest created in a two-week time span. For those submitting a bid please include front cover, theme & dates, mission & vision, and Make the Difference.

This link will provide the layout of the newsletter https://files.parcelvault.example/doc/7qzRk2LmVt9XwPa4NbHc6DsYe3FuJg8KoTiW5rQx/edit?share=1.

This link will provide you with the pictures that are needed and a few documents https://files.parcelvault.example/folders/4TpWx8QnRb2ZyLc7MfVd5HsJ?share=1

Details:
20 pages long (including covers)
8.5 x 11

Please message me if you need any further details.

Target Market(s)

Our alumni base. Covers all ages

Requirements
Must have
• Spelled out in document
Nice to have
• Spelled out in document
Should not have
• Spelled out in document

```html
<!DOCTYPE html>
<html lang="en">
<head>
<meta charset="utf-8">
<title>Camp Thornbrook – Mission, Vision &amp; Core Values</title>
<link rel="stylesheet" href="https://fonts.googleapis.com/css2?family=Ubuntu:ital,wght@0,500;0,700;1,700&family=Encode+Sans:wght@300;400;500&display=swap">
<style>
  :root{
    --ink:#1b2a22;
    --paper:#f2f3f2;
    --white:#ffffff;
    --orange:#f0a05c;
    --tan:#efd7a2;
    --green:#12794f;
    --green-text:#bfe0c9;
    --rule:#c7e4d1;
  }
  *{margin:0;padding:0;box-sizing:border-box}
  html,body{width:1200px;height:776px;overflow:hidden;background:var(--paper)}
  .spread{position:relative;width:1200px;height:776px;background:var(--paper);font-family:"Encode Sans",sans-serif;color:var(--ink)}
  .photo{position:absolute;display:block}
  .photo-cross{left:0;top:0;width:600px;height:557px;background:linear-gradient(160deg,#6f8f4a 0%,#9fb37a 35%,#b7b9ad 60%,#7d8a5e 100%)}
  .photo-cookout{left:626px;top:168px;width:184px;height:139px;background:linear-gradient(135deg,#3f5a2c,#8c8a74 60%,#b9a88a);box-shadow:3px 4px 6px rgba(0,0,0,.35)}
  .photo-gate{left:923px;top:0;width:277px;height:307px;background:linear-gradient(180deg,#e9eee8 0%,#8fb46a 45%,#2f9c52 75%,#9a7d55 100%)}
  .photo-kids{left:991px;top:323px;width:209px;height:170px;background:linear-gradient(150deg,#41532c,#7a8b55 45%,#a9b596 80%)}
  .right-wash{position:absolute;left:600px;top:0;width:600px;height:508px;background:linear-gradient(180deg,#f4f5f4 0%,#e6ebe4 60%,#9bb49d 100%)}
  .caption{position:absolute;left:20px;top:482px;width:427px;height:58px;background:var(--tan);padding:6px 0 0 10px;font-family:"Ubuntu",sans-serif;font-style:italic;font-weight:700;font-size:17.5px;line-height:21px;color:var(--ink)}
  .story{position:absolute;left:29px;top:577px;width:540px;display:flex;gap:17px;font-size:9.8px;line-height:11.8px;font-weight:400}
  .story .col{width:262px}
  .story .drop{float:left;font-size:36px;line-height:30px;font-weight:300;margin:0 3px 0 -1px}
  .heading{position:absolute;font-family:"Ubuntu",sans-serif;font-weight:700;color:var(--ink);text-align:center;line-height:1}
  .vision-band{position:absolute;left:600px;top:0;width:323px;height:61px;background:var(--paper)}
  .vision-title{left:600px;top:10px;width:310px;font-size:45px}
  .vision-box{position:absolute;left:600px;top:61px;width:322px;height:106px;background:var(--orange);text-align:center;font-family:"Ubuntu",sans-serif;font-weight:500;font-size:19.5px;line-height:29px;padding-top:8px;box-shadow:2px 3px 5px rgba(0,0,0,.25)}
  .mission-band{position:absolute;left:600px;top:323px;width:391px;height:55px;background:var(--white)}
  .mission-title{left:600px;top:330px;width:391px;font-size:45px}
  .mission-box{position:absolute;left:600px;top:378px;width:391px;height:115px;background:var(--tan);padding:6px 12px 0 19px;font-size:14.3px;line-height:16.5px;font-weight:400}
  .values-band{position:absolute;left:600px;top:508px;width:600px;height:56px;background:var(--paper)}
  .values-title{left:600px;top:515px;width:600px;font-size:46px;padding-left:0}
  .values-box{position:absolute;left:600px;top:563px;width:600px;height:213px;background:var(--green);display:flex;padding-top:12px;color:var(--green-text)}
  .values-box .col{width:300px;padding:0 8px;text-align:center;font-size:14px;line-height:16.5px;font-weight:300}
  .values-box .col p{margin-bottom:8px}
  .values-box .col + .col{border-left:1px solid var(--rule);margin-top:4px;height:184px;padding-top:0}
</style>
</head>
<body>
<main class="spread">
  <div class="photo photo-cross" role="img" aria-label="Weathered wooden cross set on a tree stump in a sunlit forest"></div>
  <div class="caption">our new mission statement, we’ve made<br>“Encountering Christ, Community, and Creation”</div>

  <section class="story">
    <div class="col">
      <p><span class="drop">L</span>ast year, we were asked by another camp director, “What is your mission statement?” We knew what we did at Camp Thornbrook, but didn’t really know how to efficiently describe what the mission looked like. This led to some self evaluation of our mission, vision, and core values.</p>
      <p>&nbsp;You may have noticed that we have been putting “Christ - Community - Creation” on everything. It’s on our new logo, it’s on almost all of our social media posts, at the end of our emails, and on all of our materials that we send out through the mail. We decided that those three things were the heart of the Thornbrook experience.</p>
      <p>This self evaluation led to the creation of our mission statement: “We want to strengthen young people’s</p>
    </div>
    <div class="col">
      <p>relationship with Christ through meaningful worship experiences, create an environment that promotes community through Christ-centered relationships, and provide opportunities to experience God’s presence through His creation.”</p>
      <p>Because of our new mission statement, we’ve made “Encountering Christ, Community, and Creation” our vision statement and tagline in hopes to help continue to promote a culture that we have all experienced and grown to love and know during our time together at Thornbrook. Our hope is that through the direction and guidance of our mission, vision, and core value statements, we will continue to carry on the legacy of mission that so many have experienced on the grounds at camp.</p>
    </div>
  </section>

  <div class="right-wash"></div>
  <div class="photo photo-gate" role="img" aria-label="Two campers in green shirts, arm in arm, facing the camp entrance gate"></div>
  <div class="photo photo-cookout" role="img" aria-label="Counselors cooking tortillas on a griddle over a campfire"></div>

  <div class="vision-band"></div>
  <h2 class="heading vision-title">Our Vision</h2>
  <div class="vision-box">Encountering Christ<br>Encountering Community<br>Encountering Creation</div>

  <div class="mission-band"></div>
  <h2 class="heading mission-title">Our Mission</h2>
  <div class="mission-box">We want to strengthen young people’s relationship with Christ through meaningful worship experiences, create an environment that promotes community through Christ-centered relationships, and provide opportunities to experience God’s presence through his creation</div>
  <div class="photo photo-kids" role="img" aria-label="Young campers outdoors holding up things they found in the woods"></div>

  <div class="values-band"></div>
  <h2 class="heading values-title">Core Values</h2>
  <section class="values-box">
    <div class="col">
      <p>We believe camp ministry to be a highly effective way to minister to young people.</p>
      <p>We teach Biblical truth in love.</p>
      <p>We believe that the glory of God can be seen and experienced through his creation in nature.</p>
      <p>We provide leadership and ministry opportunities for our counselors and staff members.</p>
    </div>
    <div class="col">
      <p>We believe that the summer camp experience provides opportunities for creating and strengthening lifelong Christ centered relationships.</p>
      <p>We believe it is important to bring glory to God by being good stewards of the gifts given to the mission of Camp Thornbrook.</p>
      <p>We want to provide the best experience possible for a reasonable price.</p>
    </div>
  </section>
</main>
</body>
</html>
```